Corvane Capital Business Cards

These are professional business cards that are for my family office.
Put fake emails and phone numbers as of now until I finalize those components. This family office controls my families investments, assets, and future. The cards should be professional.
..
.
.
.
I just uploaded another variation of a logo I would like to see as a business card to I am inbeteen which logo to use

Target Market(s)

business

Industry/Entity Type

business

Contact Information for Business Card

Professional, wealth related, finance related.

Requirements
Must have
• Logo

```html
<!DOCTYPE html>
<html lang="en">
<head>
<meta charset="UTF-8">
<title>Corvane Capital Business Card</title>
<link href="https://fonts.googleapis.com/css2?family=EB+Garamond:wght@400;500&display=swap" rel="stylesheet">
<style>
  :root {
    --backdrop: #d9d9d9;
    --card: #ffffff;
    --ink: #1c1c1c;
    --ink-soft: #3a3a3a;
    --rule: #2a2a2a;
  }
  html, body {
    margin: 0;
    width: 1200px;
    height: 900px;
    overflow: hidden;
    background: var(--backdrop);
  }
  .canvas {
    position: relative;
    width: 1200px;
    height: 900px;
  }
  .card {
    position: absolute;
    left: 180px;
    top: 210px;
    width: 840px;
    height: 480px;
    background: var(--card);
    box-shadow: 0 10px 30px rgba(0,0,0,0.12);
    font-family: "EB Garamond", Georgia, serif;
    color: var(--ink);
  }
  .brand {
    position: absolute;
    right: 60px;
    top: 70px;
    display: flex;
    align-items: center;
    gap: 14px;
  }
  .brand-dot {
    width: 34px;
    height: 34px;
    border: 2px solid var(--ink);
    border-radius: 50%;
    box-sizing: border-box;
  }
  .brand-name {
    font-size: 24px;
    font-weight: 400;
    letter-spacing: 2px;
    text-transform: uppercase;
  }
  .rule {
    position: absolute;
    height: 1.5px;
    background: var(--rule);
  }
  .rule-brand { left: 440px; right: 40px; top: 150px; }
  .rule-person { left: 40px; width: 390px; top: 318px; }
  .person {
    position: absolute;
    left: 40px;
    top: 228px;
  }
  .person-name {
    margin: 0;
    font-size: 44px;
    font-weight: 400;
    letter-spacing: 1px;
    text-transform: uppercase;
    line-height: 1;
  }
  .person-role {
    margin: 8px 0 0;
    font-size: 19px;
    color: var(--ink-soft);
  }
  .address {
    position: absolute;
    left: 40px;
    top: 334px;
    margin: 0;
    font-size: 20px;
    line-height: 1.35;
    font-style: normal;
  }
  .contact {
    position: absolute;
    left: 470px;
    top: 200px;
    margin: 0;
    padding: 0;
    list-style: none;
    font-size: 20px;
    line-height: 1.9;
  }
</style>
</head>
<body>
<div class="canvas">
  <div class="card">
    <div class="brand">
      <span class="brand-dot"></span>
      <span class="brand-name">Corvane Capital</span>
    </div>
    <div class="rule rule-brand"></div>

    <div class="person">
      <h1 class="person-name">Elias Marlow</h1>
      <p class="person-role">Manager</p>
    </div>
    <div class="rule rule-person"></div>
    <address class="address">4180 Harbor Ridge Rd Kenmore,<br>Oregon. 97310, USA</address>

    <ul class="contact">
      <li>P:+1 555 014 287</li>
      <li>M:info@corvanecapital.com</li>
      <li>W:www.corvanecapital.com</li>
    </ul>
  </div>
</div>
</body>
</html>
```